Indy Film Production Company/Studio

We need a business card designed from an existing logo. We are a digital studio/production company that caters to creating genre entertainment, like Action, Horror, and martial arts. The card along with the logo will be used to Brand the company from letter heads to banners. The design will also be used for postcards and Brochures. It should be professional and masculine.
Updates

Thank you to all the designers who have participated. I'm narrowing down who it will be. Thank you again.

Target Market(s)

Investors, Networks, Producers, and actors

Industry/Entity Type

Film Production

Contact Information for Business Card

Teodoro Valbuena
Producer/Writer/Director
www.kestrelpicturehouse.example

Requirements
Must have
• Website address, Facebook icon and Twitter icon possibly in the back of the card.
Nice to have
• Logline of Company: Follow The Action.

```html
<!DOCTYPE html>
<html lang="en">
<head>
<meta charset="utf-8">
<title>Kestrel Picture House – Business Card</title>
<link rel="stylesheet" href="https://fonts.googleapis.com/css2?family=Roboto:wght@300;400;900&display=swap">
<style>
  :root {
    --brand-red: #ec1c24;
    --brand-red-deep: #d7141c;
    --paper: #ffffff;
    --ink-grey: #5a5a5a;
    --ink-dark: #2b2b2b;
    --backdrop: #e9e7e3;
  }
  * { box-sizing: border-box; margin: 0; padding: 0; }
  html, body {
    width: 1200px; height: 950px; overflow: hidden;
    background: var(--backdrop);
    font-family: "Roboto", Arial, sans-serif;
  }
  .stage { position: relative; width: 1200px; height: 950px; }

  .card {
    position: absolute;
    width: 660px; height: 378px;
    border-radius: 4px;
    box-shadow: 0 10px 28px rgba(0,0,0,.18);
  }

  /* Front */
  .card--front {
    left: 80px; top: 60px;
    background: linear-gradient(135deg, var(--brand-red) 0%, var(--brand-red-deep) 100%);
    color: var(--paper);
  }
  .social-badges {
    position: absolute; top: 18px; right: 20px;
    display: flex; gap: 4px;
  }
  .social-badges span {
    width: 22px; height: 22px; background: var(--ink-dark); display: block;
  }
  .front-wordmark {
    position: absolute; left: 0; right: 0; top: 128px;
    text-align: center;
    font-weight: 900; font-size: 44px; line-height: 1.05;
    letter-spacing: 1px; text-transform: uppercase;
  }
  .front-web {
    position: absolute; left: 0; right: 0; top: 268px;
    text-align: center;
    font-weight: 400; font-size: 17px; letter-spacing: 2px;
  }

  /* Back */
  .card--back {
    left: 460px; top: 500px;
    background: var(--paper);
  }
  .back-wordmark {
    position: absolute; right: 34px; top: 46px;
    text-align: right;
    color: var(--brand-red);
    font-weight: 900; font-size: 36px; line-height: 1.05;
    text-transform: uppercase; letter-spacing: 1px;
  }
  .back-rule {
    position: absolute; left: 34px; right: 34px; top: 168px;
    height: 2px; background: var(--brand-red);
  }
  .back-web {
    position: absolute; right: 34px; top: 180px;
    display: flex; align-items: center; gap: 6px;
    color: var(--ink-grey); font-size: 15px;
  }
  .identity {
    position: absolute; left: 34px; bottom: 70px;
    font-size: 20px;
  }
  .identity .person { color: var(--brand-red); font-weight: 400; }
  .identity .role { color: var(--ink-grey); font-weight: 300; }
  .contacts {
    position: absolute; left: 34px; bottom: 36px;
    display: flex; align-items: center; gap: 20px;
    color: var(--ink-grey); font-size: 15px;
  }
  .contact { display: flex; align-items: center; gap: 6px; }
  .contact svg { width: 15px; height: 15px; fill: var(--brand-red); flex: none; }
  .back-web svg { width: 15px; height: 15px; fill: var(--brand-red); }
</style>
</head>
<body>
<main class="stage">

  <section class="card card--front" aria-label="Card front">
    <div class="social-badges" aria-hidden="true"><span></span><span></span></div>
    <h1 class="front-wordmark">Kestrel<br>Picture House</h1>
    <p class="front-web">www.kestrelpicturehouse.example</p>
  </section>

  <section class="card card--back" aria-label="Card back">
    <p class="back-wordmark">Kestrel<br>Picture House</p>
    <div class="back-rule"></div>
    <p class="back-web">
      <svg viewBox="0 0 16 16" aria-hidden="true"><circle cx="8" cy="8" r="8"/><path d="M6 4l5 4-5 4z" fill="#fff"/></svg>
      www.kestrelpicturehouse.example
    </p>
    <p class="identity">
      <span class="person">Teodoro Valbuena -</span>
      <span class="role">Producer/Writer/Director</span>
    </p>
    <div class="contacts">
      <span class="contact">
        <svg viewBox="0 0 16 16" aria-hidden="true"><path d="M3 1h3l1.5 4-2 1.3a9 9 0 0 0 4.2 4.2L11 8.5l4 1.5v3c0 1-1 2-2 2C6.4 15 1 9.6 1 3c0-1 1-2 2-2z"/></svg>
        555 0147 2290
      </span>
      <span class="contact">
        <svg viewBox="0 0 16 16" aria-hidden="true"><path d="M1 3h14v10H1z"/><path d="M1 3l7 6 7-6" fill="none" stroke="#fff" stroke-width="1.4"/></svg>
        hello@kestrelpicturehouse.example
      </span>
    </div>
  </section>

</main>
</body>
</html>
```